Modern Verdell Tree Care Website

I need a website for a full service Tree Care company. The company provides tree pruning, tree removal, tree preservation, emergency services, stump grinding, and emergency tree services.

Target Market(s)

Customers that need tree services

Industry/Entity Type

Landscaping, Tree Services

Coding

Coded - Design and coding required

Number of Pages Required

5+ page

Font styles to use
Sans Serif

Requirements
Must have
• Good clean design that showcases the services the company provides.
Nice to have
• Services page; contact form, blog, home page, about page

```html
<!DOCTYPE html>
<html lang="en">
<head>
<meta charset="utf-8">
<title>Verdell Tree Care</title>
<link href="https://fonts.googleapis.com/css2?family=Montserrat:wght@400;500;600;700;800&display=swap" rel="stylesheet">
<style>
:root{
  --green:#7ab83a;
  --green-dark:#2f5d1f;
  --orange:#f6a531;
  --ink:#2b2b2b;
  --muted:#555;
  --cream:#f1f1ea;
  --brown:#b08a55;
  --white:#fff;
}
*{margin:0;padding:0;box-sizing:border-box}
html,body{width:1200px;height:4827px;overflow:hidden;background:var(--white)}
body{font-family:'Montserrat',sans-serif;color:var(--ink)}
.page{position:relative;width:1200px;height:4827px;overflow:hidden}
.abs{position:absolute}
.heading{font-weight:600;letter-spacing:3px;text-transform:uppercase;color:var(--ink)}
.heading .accent{color:var(--green)}
.btn{position:absolute;background:var(--orange);color:var(--white);font-size:14px;font-weight:700;letter-spacing:1px;display:flex;align-items:center;justify-content:center;text-transform:uppercase}
.photo{position:absolute}
.uparrow{position:absolute;width:0;height:0;border-left:11px solid transparent;border-right:11px solid transparent;border-bottom:20px solid var(--green)}

/* header */
.site-header{position:absolute;top:0;left:0;width:1200px;height:84px;background:var(--white)}
.brand{position:absolute;left:94px;top:14px;display:flex;align-items:center;gap:12px}
.brand-mark{width:44px;height:44px;background:var(--orange)}
.brand-name{font-size:30px;font-weight:800;color:var(--green-dark);letter-spacing:1px;line-height:1}
.brand-sub{font-size:15px;font-weight:600;color:var(--green);letter-spacing:4px;margin-top:3px}
.nav{position:absolute;top:31px;left:341px;display:flex;font-size:14px;font-weight:600;letter-spacing:1.5px}
.nav a{color:var(--ink);text-decoration:none;padding:0 30px;border-left:1px solid #ccc}
.nav a:first-child{padding-left:0;border:none;color:var(--green);border-bottom:2px solid var(--green)}
.header-phone{position:absolute;left:979px;top:0;width:221px;height:84px;background:var(--green);color:var(--white);display:flex;align-items:center;gap:14px;padding-left:22px;font-size:16px;font-weight:600;line-height:1.3}

/* hero */
.hero{position:absolute;top:84px;left:0;width:1200px;height:640px}
.hero-photo{left:0;top:0;width:1200px;height:640px;background:linear-gradient(135deg,#dfeaf6 0%,#a9c7e8 45%,#6d9fd6 100%)}
.hero-kicker{left:115px;top:168px;font-size:17px;font-weight:500;letter-spacing:1px}
.hero-title{left:113px;top:196px;font-size:34px;line-height:46px}
.hero-title .boxed{background:var(--green);color:var(--white);padding:0 8px}
.hero-sub{left:115px;top:292px;font-size:18px;color:#333}

/* about */
.about-green{left:0;top:761px;width:340px;height:499px;background:var(--green)}
.about-photo{left:135px;top:812px;width:405px;height:401px;background:linear-gradient(160deg,#9cc77a,#4f7d35 60%,#e39b3a)}
.about-title{left:605px;top:812px;font-size:34px;line-height:44px}
.about-line{left:922px;top:874px;width:278px;height:1px;background:var(--orange)}
.about-dot{left:918px;top:870px;width:9px;height:9px;border-radius:50%;background:var(--orange)}
.about-text{left:613px;width:510px;font-size:15px;line-height:23.5px;color:#444}

/* services */
.services{left:0;top:1340px;width:1200px;height:756px;background:var(--cream)}
.section-title{position:absolute;width:1200px;text-align:center;font-size:34px}
.card-img{position:absolute;width:328px;height:207px;border-radius:0 0 30px 0}
.card-icon{position:absolute;width:62px;height:62px;border-radius:50%;background:var(--green);border:5px solid var(--white);display:flex;align-items:center;justify-content:center}
.card-label{position:absolute;font-size:18px;font-weight:600;letter-spacing:1px;text-transform:uppercase;line-height:22px}

/* why */
.why-point{position:absolute;width:76px;height:76px;border-radius:50%;background:var(--green);border:5px solid #e8f2dd;display:flex;align-items:center;justify-content:center}
.why-point.orange{background:var(--orange);border-color:#fbe7c7}
.why-label{position:absolute;font-size:14px;font-weight:600;letter-spacing:.5px;line-height:18px;text-transform:uppercase}

/* blogs */
.blogs{left:0;top:2756px;width:1200px;height:694px;background:var(--cream)}
.blog-card{position:absolute;background:var(--white);border:1px solid #ddd}
.blog-date{position:absolute;background:var(--green);color:var(--white);font-size:11px;font-weight:700;padding:5px 10px}
.blog-title{position:absolute;font-size:14px;font-weight:600;line-height:19px}
.blog-more{position:absolute;font-size:11px;font-weight:700;color:var(--green);text-decoration:underline}

/* testimonials */
.quote-card{position:absolute;width:340px;height:340px;border-radius:50%;border:3px solid var(--green);background:var(--white);box-shadow:0 0 0 10px #f2f7ec;text-align:center;padding:48px 38px 0}
.quote-mark{font-size:60px;font-weight:800;color:var(--orange);line-height:50px}
.quote-text{font-size:13px;line-height:23px;color:#444;margin-top:6px}
.quote-name{font-size:15px;font-weight:700;margin-top:8px}
.stars{color:var(--orange);letter-spacing:3px;font-size:20px}

/* contact */
.contact-photo{left:0;top:3880px;width:1200px;height:592px;background:linear-gradient(120deg,#6fa83b,#93c25b 45%,#5d9530)}
.field{position:absolute;background:var(--white);height:53px;display:flex;align-items:center;padding-left:22px;font-size:13px;color:#555;gap:10px}
.send{position:absolute;left:512px;top:4346px;width:195px;height:45px;background:var(--green-dark);color:var(--white);font-size:14px;font-weight:700;letter-spacing:.5px;display:flex;align-items:center;justify-content:center}

/* footer */
.foot-head{position:absolute;top:4535px;font-size:16px;font-weight:600;letter-spacing:1px;color:#333;border-left:3px solid var(--green);padding-left:10px}
.foot-links{position:absolute;left:443px;top:4582px;font-size:13px;line-height:29px}
.foot-links a{display:block;color:#333;text-decoration:none}
.foot-links a:first-child{text-decoration:underline}
.social{position:absolute;top:4572px;width:26px;height:26px;border-radius:50%;background:var(--orange)}
.copyright{left:0;top:4772px;width:1200px;height:55px;background:var(--brown);color:var(--white);font-size:13px;display:flex;align-items:center;justify-content:center}
</style>
</head>
<body>
<div class="page">

  <!-- Header -->
  <header class="site-header">
    <div class="brand">
      <div class="brand-mark"></div>
      <div><div class="brand-name">VERDELL</div><div class="brand-sub">TREE CARE</div></div>
    </div>
    <nav class="nav">
      <a href="#">HOME</a><a href="#">ABOUT US</a><a href="#">SERVICES</a><a href="#">BLOG</a><a href="#">CONTACT US</a>
    </nav>
    <div class="header-phone">
      <svg width="26" height="26" viewBox="0 0 24 24"><circle cx="12" cy="12" r="12" fill="#fff"/><path d="M8 6l2 0 1 3-1.5 1.2a8 8 0 0 0 4.3 4.3L15 13l3 1v2a2 2 0 0 1-2 2A10 10 0 0 1 6 8a2 2 0 0 1 2-2z" fill="#7ab83a"/></svg>
      <div>(555) 214-7730<br>(555) 386-4102</div>
    </div>
  </header>

  <!-- Hero -->
  <section class="hero">
    <div class="photo hero-photo" role="img" aria-label="Arborist with chainsaw cutting large tree limbs against a blue sky"></div>
    <svg class="abs" style="left:0;top:0" width="1200" height="640" viewBox="0 0 1200 640">
      <polygon points="0,630 900,560 1200,620 1200,640 0,640" fill="#fff"/>
      <polygon points="930,600 1200,540 1200,640" fill="#f6a531"/>
    </svg>
    <div class="abs hero-kicker">WELCOME TO VERDELL TREE CARE</div>
    <div class="abs heading hero-title">VERDELL FOR ALL YOUR<br><span class="boxed">TREE CARE</span> NEEDS</div>
    <div class="abs hero-sub">Serving Marlow Creek and surrounding areas.</div>
    <div class="btn" style="left:111px;top:340px;width:163px;height:45px">Contact Us</div>
  </section>

  <!-- About -->
  <section>
    <div class="abs about-green"></div>
    <div class="photo about-photo" role="img" aria-label="Arborist in orange shirt climbing a tree with ropes"></div>
    <div class="abs heading about-title">About Verdell<br><span class="accent">Tree Care</span></div>
    <div class="uparrow" style="left:852px;top:858px"></div>
    <div class="abs about-dot"></div>
    <div class="abs about-line"></div>
    <p class="abs about-text" style="top:918px">At Verdell Tree Care, we are more than just a tree service company, we are stewards of our beautiful trees. With a passion deeply rooted in arboriculture, we embark on a mission to promote the health, beauty, and safety of your trees and landscapes.</p>
    <p class="abs about-text" style="top:1031px">Whether it's expert tree trimming to enhance aesthetics, meticulous tree removal to mitigate hazards, or comprehensive tree health assessments to ensure safety , we approach each task with unwavering dedication and attention to detail.</p>
    <div class="btn" style="left:615px;top:1153px;width:152px;height:41px">Learn More</div>
  </section>

  <!-- Services -->
  <section class="abs services">
    <div class="uparrow" style="left:589px;top:47px"></div>
    <div class="heading section-title" style="top:80px">Our <span class="accent">Services</span></div>

    <div class="card-img" style="left:86px;top:152px;background:linear-gradient(135deg,#c9d2b8,#6f7f4e)" role="img" aria-label="Pruning shears cutting a branch"></div>
    <div class="card-img" style="left:431px;top:152px;background:linear-gradient(135deg,#5a4a30,#2d2417)" role="img" aria-label="Large tree trunk being removed"></div>
    <div class="abs" style="left:469px;top:202px;width:280px;font-size:12px;line-height:19px;color:#fff">Lorem ipsum dolor sit amet, consectetur adipiscing elit, sed do eiusmod tempor incididunt ut labore et dolore magna aliqua. Quis ipsum suspendisse ultrices gravida. Risus commodo viverra maecenas</div>
    <div class="card-img" style="left:778px;top:152px;background:linear-gradient(135deg,#8fb85a,#5b3f28)" role="img" aria-label="Shovel planting a young tree"></div>

    <div class="card-icon" style="left:106px;top:338px"><svg width="28" height="28" viewBox="0 0 24 24" fill="none" stroke="#fff" stroke-width="2"><path d="M4 20l10-10M14 4l6 6-4 4-6-6z"/></svg></div>
    <div class="card-icon" style="left:451px;top:338px;background:var(--orange)"><svg width="28" height="28" viewBox="0 0 24 24" fill="none" stroke="#fff" stroke-width="2"><rect x="5" y="9" width="14" height="11"/><path d="M9 9V4h6v5"/></svg></div>
    <div class="card-icon" style="left:796px;top:338px"><svg width="28" height="28" viewBox="0 0 24 24" fill="none" stroke="#fff" stroke-width="2"><path d="M12 3l7 3v6c0 4-3 7-7 9-4-2-7-5-7-9V6z"/></svg></div>
    <div class="card-label" style="left:184px;top:370px">Tree Pruning</div>
    <div class="card-label" style="left:528px;top:370px">Tree Removal</div>
    <div class="card-label" style="left:871px;top:370px">Tree Preservation</div>

    <div class="card-img" style="left:89px;top:436px;background:linear-gradient(135deg,#a9453a,#e09a2f 55%,#b78a5a)" role="img" aria-label="Stump grinding machine at work"></div>
    <div class="card-img" style="left:434px;top:436px;background:linear-gradient(135deg,#7fae4f,#3e5a2a)" role="img" aria-label="Fallen storm-damaged tree"></div>
    <div class="card-img" style="left:781px;top:436px;background:linear-gradient(135deg,#6da4d8,#3c5c3a)" role="img" aria-label="Arborist installing cables in a tree"></div>

    <div class="card-icon" style="left:109px;top:622px"><svg width="28" height="28" viewBox="0 0 24 24" fill="none" stroke="#fff" stroke-width="2"><circle cx="12" cy="12" r="7"/><path d="M12 5v14M5 12h14"/></svg></div>
    <div class="card-icon" style="left:454px;top:616px"><svg width="28" height="28" viewBox="0 0 24 24" fill="none" stroke="#fff" stroke-width="2"><path d="M4 20c4-10 10-14 16-16-2 6-6 12-16 16z"/></svg></div>
    <div class="card-icon" style="left:801px;top:616px"><svg width="28" height="28" viewBox="0 0 24 24" fill="none" stroke="#fff" stroke-width="2"><circle cx="12" cy="9" r="5"/><path d="M12 14v7"/></svg></div>
    <div class="card-label" style="left:186px;top:657px">Stump Grinding</div>
    <div class="card-label" style="left:531px;top:650px">Tree Emergency<br>Services</div>
    <div class="card-label" style="left:877px;top:652px">Cabling &amp; Bracing</div>
  </section>

  <!-- Why choose us -->
  <section>
    <svg class="abs" style="left:0;top:2096px" width="560" height="104" viewBox="0 0 560 104"><polygon points="0,0 560,0 0,104" fill="#7ab83a"/></svg>
    <div class="uparrow" style="left:598px;top:2165px"></div>
    <div class="heading section-title" style="top:2197px;left:0">Why <span class="accent">Choose Us</span></div>
    <svg class="abs" style="left:0;top:2250px" width="1200" height="460" viewBox="0 0 1200 460">
      <path d="M384 90 A235 235 0 0 0 594 413 A235 235 0 0 0 818 90" fill="none" stroke="#f6a531" stroke-width="1.5"/>
    </svg>
    <div class="photo" style="left:440px;top:2278px;width:310px;height:282px;border-radius:48% 48% 20% 20%;background:radial-gradient(circle at 50% 40%,#6fae3c,#2f6a1c 70%)" role="img" aria-label="Large healthy green tree"></div>

    <div class="why-point" style="left:346px;top:2265px"><svg width="30" height="30" viewBox="0 0 24 24" fill="none" stroke="#fff" stroke-width="2"><rect x="5" y="3" width="14" height="18"/><path d="M8 12l3 3 5-6"/></svg></div>
    <div class="why-label" style="left:170px;top:2280px;text-align:right;width:158px">Licensed and<br>Insured</div>
    <div class="why-point orange" style="left:324px;top:2409px"><svg width="30" height="30" viewBox="0 0 24 24" fill="none" stroke="#fff" stroke-width="2"><circle cx="12" cy="12" r="8"/><path d="M12 7v5l3 3"/></svg></div>
    <div class="why-label" style="left:100px;top:2433px;text-align:right;width:210px">24 Hour Emergency<br>Services</div>
    <div class="why-point" style="left:388px;top:2550px"><svg width="30" height="30" viewBox="0 0 24 24" fill="none" stroke="#fff" stroke-width="2"><path d="M12 21s-6-6-6-11a6 6 0 0 1 12 0c0 5-6 11-6 11z"/><circle cx="12" cy="10" r="2"/></svg></div>
    <div class="why-label" style="left:176px;top:2578px;text-align:right;width:198px">Locally Owned<br>&amp; Operated</div>
    <div class="why-point orange" style="left:556px;top:2625px"><svg width="30" height="30" viewBox="0 0 24 24" fill="none" stroke="#fff" stroke-width="2"><circle cx="12" cy="8" r="3"/><path d="M6 20c0-4 3-6 6-6s6 2 6 6"/></svg></div>
    <div class="why-label" style="left:480px;top:2712px;text-align:center;width:230px">Licensed Arborist<br>on Staff</div>
    <div class="why-point" style="left:750px;top:2559px"><svg width="30" height="30" viewBox="0 0 24 24" fill="none" stroke="#fff" stroke-width="2"><rect x="5" y="3" width="14" height="18"/><path d="M8 8h8M8 12h8M8 16h5"/></svg></div>
    <div class="why-label" style="left:836px;top:2590px">Free Estimate</div>
    <div class="why-point orange" style="left:802px;top:2409px"><svg width="30" height="30" viewBox="0 0 24 24" fill="none" stroke="#fff" stroke-width="2"><path d="M5 14a7 7 0 0 1 14 0zM4 17h16"/></svg></div>
    <div class="why-label" style="left:891px;top:2432px">Safety is our<br>top priority</div>
    <div class="why-point" style="left:780px;top:2268px"><svg width="30" height="30" viewBox="0 0 24 24" fill="none" stroke="#fff" stroke-width="2"><circle cx="12" cy="9" r="6"/><path d="M12 15v6M8 21h8"/></svg></div>
    <div class="why-label" style="left:866px;top:2288px">Professional<br>Work</div>
  </section>

  <!-- Blogs -->
  <section class="abs blogs">
    <svg class="abs" style="left:0;top:0" width="1200" height="100" viewBox="0 0 1200 100"><polygon points="830,60 1200,0 1200,100" fill="#f6a531"/></svg>
    <div class="uparrow" style="left:585px;top:78px"></div>
    <div class="heading section-title" style="top:112px">Latest <span class="accent">Blogs</span></div>

    <div class="blog-card" style="left:105px;top:203px;width:474px;height:407px">
      <div class="photo" style="left:0;top:0;width:472px;height:284px;background:linear-gradient(120deg,#c7c7c2,#7b6a52 60%,#4c4538)" role="img" aria-label="Arborist cutting a tree trunk with a chainsaw"></div>
      <div class="blog-date" style="left:16px;top:265px">20 MAY 2024</div>
      <div class="blog-title" style="left:38px;top:318px;width:400px;font-size:18px;line-height:26px">Lorem ipsum dolor sit amet consectetur adipiscing elit sed do eiusmod</div>
      <div class="blog-more" style="left:38px;top:374px;font-size:13px">LEARN MORE</div>
    </div>

    <div class="blog-card" style="left:600px;top:203px;width:500px;height:193px">
      <div class="photo" style="left:0;top:0;width:235px;height:191px;background:linear-gradient(135deg,#dfe6d5,#6f7a55)" role="img" aria-label="Climber in harness on a tree"></div>
      <div class="blog-date" style="left:262px;top:42px">30 MAY 2024</div>
      <div class="blog-title" style="left:262px;top:78px;width:210px">Lorem ipsum dolor sit amet consectetur adipiscing elit sed do eiusmod</div>
      <div class="blog-more" style="left:262px;top:146px">LEARN MORE</div>
    </div>
    <div class="blog-card" style="left:600px;top:415px;width:500px;height:195px">
      <div class="photo" style="left:0;top:0;width:235px;height:193px;background:linear-gradient(135deg,#cfd8c2,#7da049)" role="img" aria-label="Person pruning branches with loppers"></div>
      <div class="blog-date" style="left:266px;top:42px">10 MAY 2024</div>
      <div class="blog-title" style="left:266px;top:78px;width:210px">Lorem ipsum dolor sit amet consectetur adipiscing elit sed do eiusmod</div>
      <div class="blog-more" style="left:266px;top:146px">LEARN MORE</div>
    </div>
  </section>

  <!-- Testimonials -->
  <section>
    <div class="abs heading" style="left:115px;top:3555px;font-size:27px;line-height:36px;letter-spacing:2px">What People<br>Are Saying<br>About Us</div>
    <div class="uparrow" style="left:290px;top:3622px"></div>
    <div class="abs" style="left:115px;top:3695px;font-size:15px;font-weight:700">EXLLENT SERVICE</div>
    <div class="abs stars" style="left:113px;top:3717px;font-size:24px">★★★★★</div>
    <div class="abs" style="left:115px;top:3756px;font-size:13px;color:#555">4.8 Rating &nbsp;|&nbsp; 3500 Reviews</div>

    <svg class="abs" style="left:378px;top:3660px" width="16" height="28" viewBox="0 0 16 28"><path d="M13 3L3 14l10 11" fill="none" stroke="#7ab83a" stroke-width="3"/></svg>
    <svg class="abs" style="left:1092px;top:3660px" width="16" height="28" viewBox="0 0 16 28"><path d="M3 3l10 11L3 25" fill="none" stroke="#7ab83a" stroke-width="3"/></svg>

    <div class="quote-card" style="left:424px;top:3505px">
      <div class="quote-mark">“</div>
      <p class="quote-text">“Lorem ipsum dolor sit amet, consectetur adipiscing elit, sed do eiusmod tempor incididunt ut labore et dolore magna aliqua Quis ipsum suspendisse ultrices gravida Risus commodo viverra maecenas ”</p>
      <div class="quote-name">Daniel Hale</div>
      <div class="stars">★★★★★</div>
    </div>
    <div class="quote-card" style="left:762px;top:3505px">
      <div class="quote-mark">“</div>
      <p class="quote-text">“Lorem ipsum dolor sit amet, consectetur adipiscing elit, sed do eiusmod tempor incididunt ut labore et dolore magna aliqua Quis ipsum suspendisse ultrices gravida Risus commodo viverra maecenas ”</p>
      <div class="quote-name">Daniel Hale</div>
      <div class="stars">★★★★★</div>
    </div>
    <div class="quote-card" style="left:1120px;top:3505px"></div>
  </section>

  <!-- Contact -->
  <section>
    <div class="photo contact-photo" role="img" aria-label="Arborists trimming trees from a bucket lift, with green overlay"></div>
    <svg class="abs" style="left:0;top:3870px" width="1200" height="100" viewBox="0 0 1200 100">
      <polygon points="0,-10 1200,-10 1200,5 0,90" fill="#fff"/>
      <polygon points="0,0 330,80 0,80" fill="#f6a531"/>
      <polygon points="820,40 1200,0 1200,40" fill="#f6a531"/>
    </svg>
    <div class="uparrow" style="left:590px;top:3978px;border-bottom-color:#fff"></div>
    <div class="heading section-title" style="top:4012px;left:0;color:#fff">Contact Us</div>
    <div class="field" style="left:259px;top:4078px;width:340px"><svg width="12" height="12" viewBox="0 0 12 12"><circle cx="6" cy="3.5" r="2.5" fill="#888"/><path d="M1 12c0-3 2-5 5-5s5 2 5 5z" fill="#888"/></svg>First Name*</div>
    <div class="field" style="left:611px;top:4078px;width:340px"><svg width="12" height="12" viewBox="0 0 12 12"><circle cx="6" cy="3.5" r="2.5" fill="#888"/><path d="M1 12c0-3 2-5 5-5s5 2 5 5z" fill="#888"/></svg>Last Name*</div>
    <div class="field" style="left:259px;top:4142px;width:340px"><svg width="13" height="10" viewBox="0 0 13 10"><rect x=".5" y=".5" width="12" height="9" fill="none" stroke="#888"/><path d="M.5.5l6 5 6-5" fill="none" stroke="#888"/></svg>Email address</div>
    <div class="field" style="left:611px;top:4142px;width:340px"><svg width="12" height="12" viewBox="0 0 24 24"><path d="M6 3l3 0 1.5 4.5-2 1.5a11 11 0 0 0 6.5 6.5l1.5-2L21 15v3a3 3 0 0 1-3 3A15 15 0 0 1 3 6a3 3 0 0 1 3-3z" fill="#888"/></svg>Phone number</div>
    <div class="field" style="left:259px;top:4206px;width:692px;height:122px;align-items:flex-start;padding-top:16px"><svg width="13" height="12" viewBox="0 0 13 12"><path d="M1 1h11v7H5l-3 3V8H1z" fill="#888"/></svg>Leave Message</div>
    <div class="send">SEND MESSAGE</div>
  </section>

  <!-- Footer -->
  <footer>
    <div class="abs" style="left:120px;top:4540px;display:flex;align-items:center;gap:14px">
      <div style="width:56px;height:56px;background:var(--orange)"></div>
      <div><div style="font-size:40px;font-weight:800;color:var(--green-dark);letter-spacing:2px;line-height:1">VERDELL</div><div style="font-size:21px;font-weight:600;color:var(--green);letter-spacing:6px">TREE CARE</div></div>
    </div>
    <div class="foot-head" style="left:431px">NAVIGATION</div>
    <div class="foot-links"><a href="#">Home</a><a href="#">About Us</a><a href="#">Services</a><a href="#">Blogs</a><a href="#">Contact</a></div>
    <div class="foot-head" style="left:651px">CONTACT US</div>
    <svg class="abs" style="left:665px;top:4590px" width="26" height="26" viewBox="0 0 24 24"><path d="M6 3l3 0 1.5 4.5-2 1.5a11 11 0 0 0 6.5 6.5l1.5-2L21 15v3a3 3 0 0 1-3 3A15 15 0 0 1 3 6a3 3 0 0 1 3-3z" fill="none" stroke="#888" stroke-width="1.5"/></svg>
    <div class="abs" style="left:706px;top:4578px;font-size:12px;line-height:17px;color:#555">Phone number<br><b style="color:#222">(555) 214-7730<br>(555) 386-4102</b></div>
    <svg class="abs" style="left:665px;top:4660px" width="26" height="20" viewBox="0 0 26 20"><rect x="1" y="1" width="24" height="18" fill="none" stroke="#888" stroke-width="1.5"/><path d="M1 1l12 10L25 1" fill="none" stroke="#888" stroke-width="1.5"/></svg>
    <div class="abs" style="left:706px;top:4650px;font-size:12px;line-height:17px;color:#555">Email address<br><b style="color:#222">hello@verdelltreecare.com</b></div>
    <div class="foot-head" style="left:924px">FOLLOW US</div>
    <div class="social" style="left:940px"></div>
    <div class="social" style="left:979px"></div>
    <div class="social" style="left:1018px"></div>
    <div class="social" style="left:1057px"></div>
    <div class="abs copyright">Copyright © 2024 Verdell Tree Care All Right Reserved</div>
  </footer>

</div>
</body>
</html>
```